Tobias Ränkel and Co stationary design

Name of business:
Tobias Ränkel and Co

Can be written as:
Tobias Ränkel and Co
Tobias Ränkel & Co
tobias ränkel & co

If broken into letters:
TR&Co
tr&co

We are a Railway Safety Training Company
Our focus is on rail safety, Rail Management, Safety Management, Train Control Training, Accident Investigation.

.

Project Deadline Extended Reason: The original date was set to commence as soon as the logo contest finished. Sketch harbor started the project as soon as it was paid. Added Thursday, May 12, 2016

Target Market(s)

Professionals, CEO's and Managing Directors

Industry/Entity Type

Management Consulting

Font styles to use
Sans Serif

Requirements
Must have
• Professional, Sharp, Creative and modern
• Please note that this is for stationary concept which must include
• - business card
• - letterhead
• - envelope
• - with compliments slip
• - document cover (like book or folder cover)
• - dividers for folders....
• These must all have a common theme or style
Nice to have
• Keep if fresh
Should not have
• Please don't sent just fonts.... Must be creative

```html
<!DOCTYPE html>
<html lang="en">
<head>
<meta charset="utf-8">
<title>Tobias Ränkel &amp; Co — Stationery</title>
<link href="https://fonts.googleapis.com/css2?family=Kanit:wght@500&family=Open+Sans:wght@400;600&family=Pinyon+Script&display=swap" rel="stylesheet">
<style>
:root{
  --navy:#2b3a67;
  --red:#be1e36;
  --paper:#ffffff;
  --ground:#eeeeee;
  --ink:#3d4660;
  --soft:#dfe2ea;
}
*{box-sizing:border-box;margin:0;padding:0}
html,body{width:1200px;height:802px;overflow:hidden;background:var(--ground)}
body{position:relative;font-family:"Open Sans",sans-serif;color:var(--ink)}
.sheet{position:absolute;background:var(--paper);overflow:hidden}
.sheet--navy{background:var(--navy)}

/* brand lockup */
.brand{display:flex;align-items:center;gap:6px;font-family:"Kanit",sans-serif;font-weight:500;color:var(--navy);white-space:nowrap}
.brand__dot{width:9px;height:9px;border-radius:50%;background:var(--red);flex:none}
.brand--light{color:#ffffff}
.brand--stack{flex-direction:column;gap:5px}

/* footer band */
.band{position:absolute;left:0;right:0;bottom:0;height:10px}
.band__line{position:absolute;left:0;right:0;bottom:0;height:3px;background:var(--navy)}
.band__tag{position:absolute;right:0;bottom:0;height:10px;width:32%;background:var(--red);clip-path:polygon(6% 0,100% 0,100% 100%,0 100%);color:#fff;font-size:5px;letter-spacing:1.2px;display:flex;align-items:center;justify-content:center}

.contact{position:absolute;text-align:right;font-size:4.6px;line-height:7.2px;color:var(--ink)}
.contact--left{text-align:left}
.contact .ico{display:inline-block;width:4px;height:4px;background:var(--navy);margin-left:3px;vertical-align:middle;border-radius:1px}
.contact--left .ico{margin:0 3px 0 0}

/* letterhead */
.letterhead{left:186px;top:100px;width:294px;height:418px}
.letterhead .brand{position:absolute;left:20px;top:24px;font-size:9px}
.letterhead .contact{right:16px;top:12px}

/* folder cover */
.folder{left:532px;top:80px;width:348px;height:442px}
.folder__spine{position:absolute;left:0;top:0;bottom:0;width:19px;background:var(--red)}
.folder .brand{position:absolute;left:19px;right:0;top:240px;justify-content:center;font-size:17px}
.folder .brand__dot{width:14px;height:14px}

/* business cards */
.card-front{left:940px;top:340px;width:132px;height:75px}
.card-front .brand{position:absolute;left:8px;top:32px;font-size:5.4px;gap:3px}
.card-front .brand__dot{width:6px;height:6px}
.card-front__name{position:absolute;left:76px;top:14px;font-family:"Kanit",sans-serif;font-size:4.8px;color:var(--navy)}
.card-front__role{position:absolute;left:76px;top:20px;font-size:3.4px;color:var(--red)}
.card-front .contact{left:76px;top:26px;font-size:3px;line-height:4.6px}
.card-front .contact .ico{width:2.6px;height:2.6px}
.card-back{left:938px;top:437px;width:134px;height:75px}
.card-back .brand{position:absolute;inset:0;justify-content:center;font-size:6px;gap:3px}
.card-back .brand__dot{width:6px;height:6px}

/* envelope front */
.envelope{left:86px;top:566px;width:330px;height:159px}
.envelope .brand{position:absolute;left:12px;top:44px;font-size:7.6px}
.envelope .contact{left:12px;top:58px}

/* envelope back */
.envelope-back{left:449px;top:566px;width:331px;height:159px}
.envelope-back__flap{position:absolute;left:0;right:0;top:0;height:56px;background:var(--navy);clip-path:polygon(0 0,100% 0,98% 100%,2% 100%)}
.envelope-back__flap .brand{position:absolute;left:0;right:0;top:18px;justify-content:center;font-size:7px}
.envelope-back__web{position:absolute;left:0;right:0;top:40px;text-align:center;font-size:4px;color:#dfe2ea}

/* compliments slip */
.slip{left:810px;top:566px;width:332px;height:159px}
.slip .brand{position:absolute;left:16px;top:46px;font-size:7.6px}
.slip .contact{left:258px;top:10px;padding-left:5px;border-left:0.6px solid var(--soft)}
.slip__script{position:absolute;left:90px;top:82px;font-family:"Pinyon Script",cursive;font-size:27px;color:var(--navy)}
</style>
</head>
<body>

<section class="sheet letterhead" aria-label="Letterhead">
  <div class="brand"><span class="brand__dot"></span>Tobias Ränkel &amp; Co</div>
  <address class="contact">
    2140 Larchmont Road<br>Fairview, Oregon 50218<br>
    614 302 7751<span class="ico"></span><br>
    728 519 4406<span class="ico"></span><br>
    390 265 8813<span class="ico"></span><br>
    office@trcomail.com<span class="ico"></span>
  </address>
  <div class="band"><span class="band__line"></span><span class="band__tag">www.trcorail.com</span></div>
</section>

<section class="sheet sheet--navy folder" aria-label="Document cover">
  <div class="folder__spine"></div>
  <div class="brand brand--light"><span class="brand__dot"></span>Tobias Ränkel &amp; Co</div>
</section>

<section class="sheet card-front" aria-label="Business card front">
  <div class="brand"><span class="brand__dot"></span>Tobias Ränkel &amp; Co</div>
  <div class="card-front__name">Lena Hartwig</div>
  <div class="card-front__role">CEO/Founder</div>
  <address class="contact contact--left">
    2140 Larchmont Road<br>Fairview, Oregon 50218<br>
    <span class="ico"></span>614 302 7751<br>
    <span class="ico"></span>728 519 4406<br>
    <span class="ico"></span>390 265 8813<br>
    <span class="ico"></span>office@trcomail.com<br>
    <span class="ico"></span>www.trcorail.com
  </address>
</section>

<section class="sheet sheet--navy card-back" aria-label="Business card back">
  <div class="brand brand--light"><span class="brand__dot"></span>Tobias Ränkel &amp; Co</div>
</section>

<section class="sheet envelope" aria-label="Envelope front">
  <div class="brand"><span class="brand__dot"></span>Tobias Ränkel &amp; Co</div>
  <address class="contact contact--left">2140 Larchmont Road<br>Fairview, Oregon 50218</address>
  <div class="band"><span class="band__line"></span><span class="band__tag">www.trcorail.com</span></div>
</section>

<section class="sheet envelope-back" aria-label="Envelope back">
  <div class="envelope-back__flap">
    <div class="brand brand--light"><span class="brand__dot"></span>Tobias Ränkel &amp; Co</div>
    <div class="envelope-back__web">www.trcorail.com</div>
  </div>
</section>

<section class="sheet slip" aria-label="With compliments slip">
  <div class="brand"><span class="brand__dot"></span>Tobias Ränkel &amp; Co</div>
  <address class="contact contact--left">
    2140 Larchmont Road<br>Fairview, Oregon 50218<br>
    <span class="ico"></span>614 302 7751<br>
    <span class="ico"></span>728 519 4406<br>
    <span class="ico"></span>390 265 8813<br>
    <span class="ico"></span>office@trcomail.com
  </address>
  <p class="slip__script">With Compliments</p>
  <div class="band"><span class="band__line"></span><span class="band__tag">www.trcorail.com</span></div>
</section>

</body>
</html>
```